Harborview Estates Business Card for Apartment Buildings

Create business cards for resident managers who run apartment buildings. The audience is the public who are searching for apartment rentals, and current residents who live at the apartment building. Key design element will be incorporating the company logo, however, the logo cannot dominate. The building name and manager name are more important than the logo. Current business card design leaves little room for copy, so we may need to reduce the size on the current card to allow for more space for copy.

Target Market(s)

Adults 18-65 years of age, who are looking for an apartment rental, plus current residents who live at our apartment buildings.

Industry/Entity Type

Property Management

Contact Information for Business Card

A major design element will be use of the company logo. Important property and manager contact information must be part of the design. The size of the logo will need to be reduced to make room for building and manager contact copy.

Font styles to use
Sans Serif

Colors
3176b5
000000
959595
ffffff

Requirements
Must have
• 1) Incorporate the company logo.
• 2) Use the company colors (dark blue, black/grey, over white).
• 3) FEATURE THE BUILDING NAME
• 4) FEATURE THE MANAGER NAME
• 5) The company name is less important than BUILDING and MANAGER
• 6) Manager contact information
• **SEE ATTACHED CREATIVE BRIEF**
Nice to have
• 1) Back of card logo watermark
• 2) Ability to write notes on back of carfd
Should not have
• Avoid letting the company logo dominate the card, the building name and manager are more important than the company logo.

```html
<!DOCTYPE html>
<html lang="en">
<head>
<meta charset="utf-8">
<title>Harborview Estates Business Card</title>
<link href="https://fonts.googleapis.com/css2?family=Lato:wght@400;700;900&display=swap" rel="stylesheet">
<style>
  :root {
    --stage: #1f1f1f;
    --card-front: #ececec;
    --card-back: #ffffff;
    --brand-blue: #1a67a8;
    --ink: #222222;
    --rule: #a6a6a6;
    --watermark: #ececec;
  }
  * { margin: 0; padding: 0; box-sizing: border-box; }
  html, body {
    width: 1200px; height: 900px; overflow: hidden;
    background: var(--stage);
    font-family: "Lato", Arial, sans-serif;
  }
  .stage { position: relative; width: 1200px; height: 900px; }
  .card {
    position: absolute; top: 170px; width: 347px; height: 561px;
    box-shadow: 3px 4px 8px rgba(0,0,0,0.55);
    overflow: hidden;
  }
  .card--front { left: 259px; background: var(--card-front); }
  .card--back { left: 631px; background: var(--card-back); }

  .brand {
    position: absolute; top: 128px; left: 0; right: 0;
    display: flex; align-items: center; justify-content: center; gap: 10px;
  }
  .brand__mark { width: 22px; height: 22px; background: var(--brand-blue); }
  .brand__name {
    font-weight: 900; color: var(--brand-blue);
    font-size: 27px; letter-spacing: 0.5px; line-height: 1;
  }

  .contact { position: absolute; top: 302px; left: 0; right: 0; text-align: center; color: var(--ink); }
  .contact__name { font-weight: 700; font-size: 24px; color: var(--brand-blue); letter-spacing: 0.3px; line-height: 30px; }
  .contact__role { font-size: 15px; line-height: 18px; }
  .contact__rule { width: 198px; height: 1px; background: var(--rule); margin: 11px auto 13px; }
  .contact__lines { font-size: 15px; line-height: 20px; }
  .contact__label { font-weight: 700; color: var(--brand-blue); }
  .contact__web { color: var(--brand-blue); }
  .contact__rule--lower { margin: 10px auto 12px; }
  .contact__address { font-size: 15px; line-height: 20px; }

  .watermark { position: absolute; left: 0; top: 0; }
</style>
</head>
<body>
<main class="stage">
  <section class="card card--front">
    <div class="brand">
      <span class="brand__mark"></span>
      <span class="brand__name">HARBORVIEW ESTATES</span>
    </div>
    <div class="contact">
      <p class="contact__name">DANIEL REYES</p>
      <p class="contact__role">Property Manager</p>
      <div class="contact__rule"></div>
      <div class="contact__lines">
        <p><span class="contact__label">P:</span> 555-214-7730</p>
        <p><span class="contact__label">F:</span> 555-214-7731</p>
        <p><span class="contact__label">E:</span> daniel@harborviewestates.us</p>
        <p class="contact__web">www.harborviewestates.us</p>
      </div>
      <div class="contact__rule contact__rule--lower"></div>
      <div class="contact__address">
        <p>1280 Bayline Avenue #B210</p>
        <p>Port Calder, CA 90411</p>
      </div>
    </div>
  </section>

  <section class="card card--back">
    <svg class="watermark" width="347" height="561" viewBox="0 0 347 561" aria-hidden="true">
      <circle cx="250" cy="380" r="210" fill="none" stroke="var(--watermark)" stroke-width="14"/>
    </svg>
    <div class="brand">
      <span class="brand__mark"></span>
      <span class="brand__name">HARBORVIEW ESTATES</span>
    </div>
  </section>
</main>
</body>
</html>
```